Business Card Design For Office Furniture Clearance Company

Kestrel Office Clearance - our company name pretty much explains what we do, we clear offices for high end clients, mainly plc's and large international companies.

We require a nice looking business card that displays professionalism but without being too serious.

It would be nice to see just a little more than a conventional boring business card, make sure you add some flare.

Industry/Entity Type

Office Furniture

Contact Information for Business Card

CARD 1

Mark Holloway
Director
mark@kestrelofficeclearance.co.uk
m: 07700 153928

t: 01632 960418
www.kestrelofficeclearance.co.uk

Kestrel Office Clearance
Unit K4 B
2-8 Fenwick Lane
Harwick Vale
Ashford Mere
ZZ9 4QT

no-charge office clearing… nothing beats a deal like that.

CARD 2

Peter Radford
Director
peter@kestrelofficeclearance.co.uk
m: 07700 382615

t: 01632 960418

Kestrel Office Clearance
Unit K4 B
2-8 Fenwick Lane
Harwick Vale
Ashford Mere
ZZ9 4QT

Font styles to use
Sans Serif

Requirements
Must have
• A white background - as we have a blue logo.
Nice to have
• Nice use of the logo - play around with this and dissect it.

```html
<!DOCTYPE html>
<html lang="en">
<head>
<meta charset="utf-8">
<title>Kestrel Office Clearance – Business Cards</title>
<link rel="stylesheet" href="https://fonts.googleapis.com/css2?family=Open+Sans:wght@400;600;700&display=swap">
<style>
  :root {
    --brand-blue: #0a7cc2;
    --brand-blue-deep: #0a5c9b;
    --paper: #ffffff;
    --backdrop: #e9ecef;
    --ink-light: #ffffff;
  }
  * { margin: 0; padding: 0; box-sizing: border-box; }
  html, body {
    width: 1200px; height: 900px; overflow: hidden;
    background: var(--backdrop);
    font-family: "Open Sans", Arial, sans-serif;
  }
  .stage { position: relative; width: 1200px; height: 900px; }

  .card {
    position: absolute;
    background: var(--paper);
    overflow: hidden;
    box-shadow: 0 6px 18px rgba(0,0,0,0.15);
  }

  .brand-disc {
    position: absolute;
    border-radius: 50%; background: var(--brand-blue);
    border: 10px solid var(--paper);
    display: flex; align-items: center; justify-content: center; text-align: center;
  }
  .wordmark {
    font-weight: 700; color: var(--ink-light); line-height: 1.2;
  }

  /* Front */
  .card--front { left: 78px; top: 35px; width: 588px; height: 363px; }
  .card--front .band {
    position: absolute; left: 0; right: 0; top: 140px; bottom: 0;
    background: linear-gradient(180deg, var(--brand-blue) 0%, var(--brand-blue-deep) 100%);
  }
  .card--front .brand-disc { left: 362px; top: 8px; width: 188px; height: 188px; }
  .card--front .wordmark { font-size: 20px; }

  .contact { position: absolute; left: 31px; top: 153px; color: var(--ink-light); }
  .contact .person { font-size: 22px; font-weight: 600; line-height: 1.2; margin-bottom: 11px; }
  .contact .person .role { font-size: 15px; font-weight: 400; }
  .contact .lines { list-style: none; }
  .contact .lines li {
    display: flex; align-items: center; gap: 8px;
    font-size: 15px; line-height: 24.5px;
  }
  .contact .lines svg { width: 12px; height: 12px; fill: var(--ink-light); flex: none; }
  .contact .company { font-size: 19px; font-weight: 700; margin-top: 8px; line-height: 1.3; }
  .contact .address { font-size: 15px; line-height: 1.4; }

  /* Back */
  .card--back { left: 388px; top: 505px; width: 567px; height: 352px; }
  .card--back .band {
    position: absolute; left: 0; right: 0; top: 110px; height: 132px;
    background: linear-gradient(180deg, var(--brand-blue) 0%, var(--brand-blue-deep) 100%);
  }
  .card--back .brand-disc { left: 186px; top: 73px; width: 190px; height: 190px; }
  .card--back .wordmark { font-size: 21px; }
  .card--back .tagline {
    position: absolute; left: 0; right: 0; top: 283px; text-align: center;
    font-size: 19px; font-weight: 600; color: var(--brand-blue-deep);
  }
</style>
</head>
<body>
<main class="stage">

  <section class="card card--front" aria-label="Business card front">
    <div class="band"></div>
    <div class="brand-disc"><span class="wordmark">Kestrel<br>Office<br>Clearance</span></div>
    <div class="contact">
      <p class="person">Mark Holloway- <span class="role">Director</span></p>
      <ul class="lines">
        <li><svg viewBox="0 0 12 12" aria-hidden="true"><path d="M3 0h6a1 1 0 0 1 1 1v10a1 1 0 0 1-1 1H3a1 1 0 0 1-1-1V1a1 1 0 0 1 1-1zm0.8 1.5v8h4.4v-8z"/></svg>07700 153928</li>
        <li><svg viewBox="0 0 12 12" aria-hidden="true"><path d="M2.5 0.5l2 2.2-1 1.5c.8 1.7 2 2.9 3.8 3.8l1.5-1 2.2 2-1.2 2.2C5 11 1 7 .3 1.7z"/></svg>01632 960418</li>
        <li><svg viewBox="0 0 12 12" aria-hidden="true"><path d="M0 2h12v8H0zm1 1v.3l5 3.2 5-3.2V3z"/></svg>mark@kestrelofficeclearance.co.uk</li>
        <li><svg viewBox="0 0 12 12" aria-hidden="true"><path d="M6 0a6 6 0 1 0 0 12A6 6 0 0 0 6 0zm-3.5 3.2c1 .2 1.6.9 1.4 1.8-.2.8.7 1.2.6 2.2-.1.9-.9 1.2-.9 2.3A4.8 4.8 0 0 1 2.5 3.2zm4.9-1.9c-.2.7-.9 1-.7 1.8.3.9 1.4.5 1.8 1.4.4.8-.2 1.6.4 2.2.5.5 1.1.2 1.6.1A4.8 4.8 0 0 0 7.4 1.3z"/></svg>www.kestrelofficeclearance.co.uk</li>
      </ul>
      <p class="company">Kestrel Office Clearance</p>
      <p class="address">Unit K4 B, 2-8 Fenwick Lane Harwick Vale, Ashford Mere&nbsp; ZZ9 4QT</p>
    </div>
  </section>

  <section class="card card--back" aria-label="Business card back">
    <div class="band"></div>
    <div class="brand-disc"><span class="wordmark">Kestrel<br>Office<br>Clearance</span></div>
    <p class="tagline">no-charge office clearing… nothing beats a deal like that</p>
  </section>

</main>
</body>
</html>
```